Business Card Design for Vintage Jazz

I am a vintage jazz band leader in New York City. My groups play the music of the 1920s, 1930s and 1940s. My website is morvalquist.com for more info on what I do.

I am looking for a two sided business card design that has the look and feel of a really nice business card from the 1930s. I need to convey with the design that my work has that vintage kind of class and style, but also conveys that we are fun and entertaining.

Most importantly it should make a bold staement. If Hal Denbrook had a card, what would it have looked like? I want a card that I feel confident will make an impact and will let people know that my work is te the top that NYC has to offer in vintage jazz..

Note that I have only decided to avoid the "committed payment" option as I have not used this service before. Assuming that I get quality work I will select a design from those presented.

Target Market(s)

people who want to hire my band for events, media, and new fans of the band

Industry/Entity Type

Performing Art

Contact Information for Business Card

Definitely a matte finish, possibly a sort of old style of paper with that brown tint? definitely a thick card.

Requirements
Must have
• FRONT
• My name: Tobin Vashley
• What I do: Bandleader, Guitarist, Vocalist, Songwriter
• Contact Details: morvalquist.com tobin@morvalquist.com 646-555-0148
• BACK
• My Social Media Links:
• facebook.morvalquist.com
• twitter, instagram, linkedin: morvalquist
• I'm also including a photo image I would like to use. The photo's background is not needed, and to be honest isn't really desireable. Just looking to use the image of me.
Nice to have
• I'm attaching which could be used as is, omitted from the card, or altered maybe with text going around the outside of the circle or in some other way. It may need some clean up to the edges of the lettering as we only use it for the website thumbnail.
• If there's space I'd like to include the text "join our mailing list for a free song download: freesong.morvalquist.com" If not perhaps just "Download a Free Song at: freesong.morvalquist.com - something to this end.
Should not have
• anything cartoony. Don't think retro 90s's vision of the swing era, think actual swing era!
• anything modern. Got to look old school
• Try to avoid dark backgrounds. Since we often play in bars and clubs where it is dar, a d
• avoid script fonts.

```html
<!DOCTYPE html>
<html lang="en">
<head>
<meta charset="utf-8">
<title>Tobin Vashley – Business Card</title>
<link rel="stylesheet" href="https://fonts.googleapis.com/css2?family=Open+Sans:wght@400;600;700&display=swap">
<style>
  :root {
    --backdrop: #e8e5e0;
    --card: #0b0b0b;
    --ink: #f2f2f2;
    --ink-soft: #cfcfcf;
    --silver: #bdbdbd;
    --photo-light: #9a9a9a;
    --photo-dark: #1c1c1c;
  }
  * { margin: 0; padding: 0; box-sizing: border-box; }
  html, body {
    width: 1200px; height: 900px; overflow: hidden;
    background: var(--backdrop);
    font-family: "Open Sans", Arial, sans-serif;
  }
  .stage { position: relative; width: 1200px; height: 900px; }
  .card {
    position: absolute; top: 295px;
    width: 540px; height: 310px;
    background: var(--card);
    border-radius: 4px;
    overflow: hidden;
    color: var(--ink);
  }
  .card--front { left: 40px; }
  .card--back { left: 620px; }

  .portrait {
    position: absolute; left: 80px; top: 90px;
    width: 230px; height: 220px;
    background: radial-gradient(ellipse at 50% 45%, var(--photo-light) 0%, #555 45%, var(--photo-dark) 100%);
  }
  .brand {
    position: absolute; left: 300px; top: 38px;
    display: flex; align-items: center; gap: 10px;
  }
  .brand__dot { width: 40px; height: 40px; border-radius: 50%; background: var(--ink); }
  .brand__name { font-size: 13px; font-weight: 600; letter-spacing: 2px; color: var(--ink); }

  .details { position: absolute; left: 300px; top: 118px; }
  .details__name { font-size: 16px; font-weight: 700; margin-bottom: 10px; }
  .details__row {
    display: flex; align-items: center; gap: 9px;
    font-size: 13px; color: var(--ink-soft); line-height: 22px;
  }
  .details__row svg { width: 11px; height: 11px; fill: var(--ink-soft); flex: none; }
  .details__roles { margin-top: 12px; font-size: 14px; line-height: 20px; color: var(--ink-soft); }

  .back-brand {
    position: absolute; left: 110px; top: 132px;
    font-size: 30px; font-weight: 400; letter-spacing: 1px; color: var(--silver);
  }
  .socials { position: absolute; left: 330px; top: 92px; }
  .socials__row {
    display: flex; align-items: center; gap: 8px;
    font-size: 12px; line-height: 21px; color: var(--ink-soft);
  }
  .socials__mark { width: 10px; height: 10px; background: var(--ink-soft); border-radius: 1px; flex: none; }
</style>
</head>
<body>
<main class="stage">
  <section class="card card--front">
    <div class="portrait" role="img" aria-label="Black and white cut-out portrait of the bandleader in a striped blazer, tipping a straw boater hat"></div>

    <div class="brand">
      <span class="brand__dot"></span>
      <span class="brand__name">MORVALQUIST</span>
    </div>

    <div class="details">
      <p class="details__name">Tobin Vashley</p>
      <p class="details__row">
        <svg viewBox="0 0 24 24" aria-hidden="true"><path d="M6.6 10.8a15 15 0 0 0 6.6 6.6l2.2-2.2a1 1 0 0 1 1-.25 11.4 11.4 0 0 0 3.6.57 1 1 0 0 1 1 1V20a1 1 0 0 1-1 1A17 17 0 0 1 3 4a1 1 0 0 1 1-1h3.5a1 1 0 0 1 1 1c0 1.25.2 2.45.57 3.57a1 1 0 0 1-.25 1z"/></svg>
        646-555-0148
      </p>
      <p class="details__row">
        <svg viewBox="0 0 24 24" aria-hidden="true"><path d="M2 5h20v14H2z M4 7v.5l8 5 8-5V7l-8 5z" fill-rule="evenodd"/></svg>
        tobin@morvalquist.com
      </p>
      <p class="details__row">
        <svg viewBox="0 0 24 24" aria-hidden="true"><path d="M12 2a10 10 0 1 0 0 20 10 10 0 0 0 0-20zm0 2c.9 0 2.2 2.1 2.7 5H9.3C9.8 6.1 11.1 4 12 4zm-7.7 7h4.8a22 22 0 0 0 0 2H4.3a8 8 0 0 1 0-2zm6.8 0h1.8a20 20 0 0 1 0 2h-1.8a20 20 0 0 1 0-2zm3.8 0h4.8a8 8 0 0 1 0 2h-4.8a22 22 0 0 0 0-2zM9.3 15h5.4c-.5 2.9-1.8 5-2.7 5s-2.2-2.1-2.7-5z"/></svg>
        morvalquist.com
      </p>
      <p class="details__roles">Bandleader, Guitarist<br>Vocalist, Songwriter</p>
    </div>
  </section>

  <section class="card card--back">
    <p class="back-brand">Morvalquist</p>
    <ul class="socials" style="list-style:none">
      <li class="socials__row"><span class="socials__mark"></span>morvalquist.com</li>
      <li class="socials__row"><span class="socials__mark"></span>morvalquist</li>
      <li class="socials__row"><span class="socials__mark"></span>morvalquist</li>
      <li class="socials__row"><span class="socials__mark"></span>morvalquist</li>
    </ul>
  </section>
</main>
</body>
</html>
```